Request for Business Card Design

Hi. My name is Marlene, I am looking for a new business card design for my company, Quarrow Signal Instruments, LLC. I really like the design you did for Tarsel Venture and was hoping you could do something similar using our full logo and our mark. I am also open to any raised texture design using our mark. I have attached our full logo, which would need to be somewhere on the card, as well as the mark in both outline and full form, as well as our brand colors / guide. The card does not have to be white, as long as our logo and mark appear. I actually like darker colored business cards more, but am open to all options. If you are interested in working with me, please let me know. We would also take the business card design into letterhead design if you can do that.

```html
<!DOCTYPE html>
<html lang="en">
<head>
<meta charset="utf-8">
<title>Quarrow Signal Instruments – Business Card</title>
<link href="https://fonts.googleapis.com/css2?family=Open+Sans:wght@400;700&display=swap" rel="stylesheet">
<style>
  :root {
    --backdrop: #3b3b3b;
    --card: #151515;
    --card-edge: #1ea3d6;
    --accent: #1ea3d6;
    --ink: #f2f2f2;
    --muted: #d9d9d9;
  }
  * { margin: 0; padding: 0; box-sizing: border-box; }
  html, body {
    width: 1200px; height: 801px; overflow: hidden;
    background: var(--backdrop);
    font-family: "Open Sans", Arial, sans-serif;
  }
  .stage { position: relative; width: 1200px; height: 801px; }
  .card {
    position: absolute;
    width: 540px; height: 309px;
    background: var(--card);
    border-bottom: 3px solid var(--card-edge);
    border-left: 2px solid var(--card-edge);
  }
  .card--front { left: 70px; top: 110px; }
  .card--back { left: 590px; top: 382px; }

  .brand {
    position: absolute; left: 42px; top: 132px;
    display: flex; align-items: center; gap: 14px;
    color: var(--ink); font-weight: 700;
  }
  .brand__dot {
    width: 40px; height: 40px; border-radius: 50%;
    background: var(--accent);
  }
  .brand__name { line-height: 1; }
  .brand__primary { display: block; font-size: 34px; letter-spacing: 2px; }
  .brand__secondary { display: block; font-size: 9.5px; letter-spacing: 0.6px; margin-top: 4px; }

  .divider {
    position: absolute; left: 300px; top: 58px;
    width: 2px; height: 192px; background: var(--accent);
  }
  .contact { position: absolute; left: 322px; top: 58px; color: var(--muted); }
  .contact__name {
    color: var(--accent); font-weight: 700; font-size: 17px;
    letter-spacing: 0.5px; text-transform: uppercase;
  }
  .contact__title { font-size: 13px; margin-bottom: 14px; }
  .contact__address { font-size: 13px; line-height: 1.45; margin-bottom: 14px; }
  .contact__list { list-style: none; font-size: 13px; line-height: 1.6; }
  .contact__list li { display: flex; align-items: center; gap: 8px; }
  .contact__icon { width: 11px; height: 11px; flex: none; }

  .pattern-field {
    position: absolute; inset: 0;
    background: linear-gradient(135deg, #0c0c0c 0%, #1a1a1a 55%, #3a3a3a 100%);
  }
  .back-dot {
    position: absolute; right: 92px; top: 130px;
    width: 66px; height: 66px; border-radius: 50%;
    background: var(--accent);
  }
</style>
</head>
<body>
<main class="stage">
  <section class="card card--front" aria-label="Business card front">
    <div class="brand">
      <span class="brand__dot"></span>
      <span class="brand__name">
        <span class="brand__primary">QUARROW</span>
        <span class="brand__secondary">SIGNAL INSTRUMENTS</span>
      </span>
    </div>
    <div class="divider"></div>
    <div class="contact">
      <p class="contact__name">Dorian Velko</p>
      <p class="contact__title">President</p>
      <p class="contact__address">1187 Linden Cove Road<br>Harlow Bay CA 90417</p>
      <ul class="contact__list">
        <li>
          <svg class="contact__icon" viewBox="0 0 12 12"><path fill="#1ea3d6" d="M2.5 0.5 L4.5 0.5 L5.2 3.2 L3.9 4.3 Q5 6.8 7.7 8.1 L8.8 6.8 L11.5 7.5 L11.5 9.5 Q11.5 11.5 9.5 11.5 Q0.5 11 0.5 2.5 Q0.5 0.5 2.5 0.5 Z"/></svg>
          555-318-0472
        </li>
        <li>
          <svg class="contact__icon" viewBox="0 0 12 12"><rect x="0.5" y="2" width="11" height="8" fill="#1ea3d6"/><path d="M0.8 2.4 L6 6.5 L11.2 2.4" fill="none" stroke="#151515" stroke-width="1.2"/></svg>
          d.velko@quarrow.com
        </li>
        <li>
          <svg class="contact__icon" viewBox="0 0 12 12"><circle cx="6" cy="6" r="5.5" fill="#1ea3d6"/><path d="M0.5 6 H11.5 M6 0.5 Q2.8 6 6 11.5 M6 0.5 Q9.2 6 6 11.5" fill="none" stroke="#151515" stroke-width="0.9"/></svg>
          www.quarrow.com
        </li>
      </ul>
    </div>
  </section>

  <section class="card card--back" aria-label="Business card back">
    <div class="pattern-field" role="img" aria-label="Raised-texture repeat of the company mark across the card back"></div>
    <span class="back-dot"></span>
  </section>
</main>
</body>
</html>
```